Business Card Design for Vandel Holdings

I need a business card designed for Vandel Holdings. I would like basic contact info and would like the card to be a bit modern but not childish. We manage several companies so it needs to look very professional. Watermark is cool and a plan logo maybe offset on the other side but I will leave the design up to you. I would like to see both color and grey scale designs. This is my first time using Pixel Harbor so hopefully we get some great results! Future projects available for the selected designer potentially.

Target Market(s)

Vandel Holdings owns several companies serving the software, real estate and automotive industry

Industry/Entity Type

Business

Contact Information for Business Card

Douglas R. Vandel
208.562.1437
douglas.r.vandel@mailnest.test

Font styles to use
Serif

Requirements
Must have
• contact information listed on card details
Nice to have
• I am open to letting you use your creative mind to design the best eye catching cards.

```html
<!DOCTYPE html>
<html lang="en">
<head>
<meta charset="utf-8">
<title>Vandel Holdings – Business Card</title>
<link rel="stylesheet" href="https://fonts.googleapis.com/css2?family=Arimo:wght@400;700&display=swap">
<style>
  :root{
    --bg:#2b2b2b;
    --brand-blue:#0e9dd3;
    --brand-blue-deep:#0a86b8;
    --navy:#1d3f8a;
    --paper:#ffffff;
    --paper-shade:#eeeeee;
    --ink:#1b2430;
    --name-ink:#d8e7ef;
  }
  html,body{margin:0;padding:0;width:1200px;height:873px;overflow:hidden;background:var(--bg);font-family:"Arimo",Arial,sans-serif;}
  .canvas{position:relative;width:1200px;height:873px;}
  .card{position:absolute;width:530px;height:303px;top:285px;overflow:hidden;box-shadow:0 10px 30px rgba(0,0,0,.5);}
  .card--back{left:45px;background:var(--brand-blue);display:flex;align-items:center;justify-content:center;gap:22px;}
  .card--back .mark-dot{width:74px;height:74px;border-radius:50%;background:var(--paper);}
  .card--back .brand-name{color:var(--paper);font-weight:700;font-size:40px;letter-spacing:.5px;}
  .card--front{left:625px;background:linear-gradient(180deg,var(--paper) 0%,var(--paper-shade) 100%);}
  .front__brand{position:absolute;top:32px;left:0;right:0;display:flex;align-items:center;justify-content:center;gap:12px;}
  .front__brand .mark-dot{width:38px;height:38px;border-radius:50%;background:var(--navy);}
  .front__brand .brand-name{color:var(--navy);font-weight:700;font-size:24px;}
  .front__band{position:absolute;left:0;right:0;top:138px;bottom:0;background:var(--brand-blue);}
  .front__rule{position:absolute;left:0;right:0;top:128px;height:3px;background:var(--brand-blue);}
  .front__person{position:absolute;top:146px;left:0;right:0;text-align:center;}
  .person-name{color:var(--name-ink);font-weight:700;font-size:21px;letter-spacing:.3px;text-transform:uppercase;}
  .person-title{color:var(--ink);font-size:15px;margin-top:2px;}
  .contact{position:absolute;display:flex;align-items:center;gap:8px;color:var(--ink);font-size:15px;}
  .contact svg{width:15px;height:15px;flex:none;}
  .contact--email{right:26px;top:214px;}
  .contact--phone{left:26px;bottom:24px;}
</style>
</head>
<body>
<main class="canvas">
  <section class="card card--back" aria-label="Card back">
    <span class="mark-dot"></span>
    <span class="brand-name">Vandel Holdings</span>
  </section>

  <section class="card card--front" aria-label="Card front">
    <div class="front__brand">
      <span class="mark-dot"></span>
      <span class="brand-name">Vandel Holdings</span>
    </div>
    <div class="front__rule"></div>
    <div class="front__band"></div>
    <div class="front__person">
      <div class="person-name">Douglas R. Vandel</div>
      <div class="person-title">Managing Partner</div>
    </div>
    <div class="contact contact--email">
      <svg viewBox="0 0 16 16" aria-hidden="true"><circle cx="8" cy="8" r="8" fill="#d8e7ef"/><rect x="4" y="5" width="8" height="6" fill="none" stroke="#0e9dd3" stroke-width="1.2"/><path d="M4 5l4 3.2L12 5" fill="none" stroke="#0e9dd3" stroke-width="1.2"/></svg>
      <span>douglas.r.vandel@mailnest.test</span>
    </div>
    <div class="contact contact--phone">
      <svg viewBox="0 0 16 16" aria-hidden="true"><circle cx="8" cy="8" r="8" fill="#d8e7ef"/><path d="M5 5.5c0 3 2.5 5.5 5.5 5.5l.8-1.6-1.8-.9-.8.8c-1-.5-1.8-1.3-2.3-2.3l.8-.8-.9-1.8z" fill="#0e9dd3"/></svg>
      <span>208.562.1437</span>
    </div>
  </section>
</main>
</body>
</html>
```